VANTOL GROUP

This is a company that provides executive protection. Our motto is "New Era in Protection"... I don't want this to look like other security websites. I want it to be clean and sharp and represent a new era. We are based in the bay area so maybe a picture of San Francisco in the background?
I want it to be able to funnel down a couple different categories.
1. About Us
2. Services (Executive Protection, Covert Protection, Residential Protection & Intelligence)
3. Blue Maple (Training & Consulting)
4. Contact Us
I want it to be very clean and modern. I don't want there to be any pictures of bodyguards with ear pieces like every other website.
Target Market(s)
Ultra High Net Worth Individuals
Coding
Coded - Design and coding required
Number of Pages Required
1 page
Requirements
Must have
- Colors of my Symbol
Nice to have
- City in the background, San Francisco, New York or the Pinecrest Lodge in Montana.
Should not have
- Should not look like an KVM website or have photos of bodyguards. I want this to be a clean and simple website with my logo

```html
<!DOCTYPE html>
<html lang="en">
<head>
<meta charset="utf-8">
<title>VANTOL GROUP — New Era in Protection</title>
<link href="https://fonts.googleapis.com/css2?family=Audiowide&family=Roboto:wght@400;500;700&display=swap" rel="stylesheet">
<style>
:root{
  --red:#7a0c14;
  --red-deep:#5e0910;
  --ink:#222222;
  --card-dark:#232323;
  --text:#555555;
  --paper:#ffffff;
  --mist:#f4f4f4;
  --footer:#1d1d1d;
  --rule:#3a3a3a;
}
*{box-sizing:border-box;margin:0;padding:0}
html,body{width:1200px;height:3596px;overflow:hidden;background:var(--paper)}
body{position:relative;font-family:"Roboto",Arial,sans-serif;color:var(--text)}
.abs{position:absolute}
.display{font-family:"Audiowide","Arial Black",sans-serif;font-weight:400}

/* hero */
.hero{left:0;top:0;width:1200px;height:802px;background:linear-gradient(180deg,#16223a 0%,#1f2a40 45%,#2d2a2b 70%,#1a1c24 100%)}
.brand{display:flex;align-items:center;gap:14px;color:#fff}
.brand-square{width:52px;height:52px;border:3px solid #fff}
.brand-name{font-family:"Audiowide",sans-serif;line-height:1;color:#fff}
.brand-name .l1{display:block;font-size:38px;letter-spacing:1px}
.brand-name .l2{display:block;font-size:17px;letter-spacing:10px;margin-top:6px;padding-left:44px}
.topnav{left:506px;top:64px;display:flex;gap:46px}
.topnav a,.footnav a{font-family:"Audiowide",sans-serif;font-size:15px;color:#fff;text-decoration:none}
.hero-title{left:0;width:1200px;top:362px;text-align:center;font-size:78px;color:#fff;letter-spacing:2px}
.hero-sub{left:0;width:1200px;top:468px;text-align:center;font-size:18px;line-height:38px;color:#fff}

/* services */
.section-title{font-size:33px;color:var(--ink);text-align:center;left:0;width:1200px;top:870px}
.section-title span{color:var(--red)}
.title-rule{left:576px;top:923px;width:48px;height:3px;background:var(--red)}
.card{top:971px;width:232px;height:361px;border-radius:10px;text-align:center;color:#fff;padding-top:36px}
.card.red{background:var(--red)}
.card.dark{background:var(--card-dark)}
.card svg{display:block;margin:0 auto;width:92px;height:92px}
.card h3{font-weight:700;font-size:21px;margin-top:20px;letter-spacing:.5px}
.card .kind{font-size:15px;margin-top:3px;color:#e6e6e6;height:18px}
.card p{font-size:13.5px;line-height:23px;margin-top:12px;padding:0 14px}
.pill{display:inline-block;border:1.5px solid #fff;border-radius:24px;color:#fff;font-size:12.5px;font-weight:500;padding:14px 23px;margin-top:16px}

/* welcome */
.welcome{left:0;top:1400px;width:1200px;height:539px;background:linear-gradient(180deg,var(--red) 0%,#6a1016 55%,var(--red-deep) 100%)}
.welcome-photo{left:162px;top:1476px;width:382px;height:407px;background:linear-gradient(135deg,#e9e4e1,#c9b8b0 55%,#efe9e6)}
.welcome-h{left:639px;color:#fff}
.welcome-copy{left:639px;top:1608px;width:372px;font-size:13.6px;line-height:25.8px;color:#fff;text-align:justify}
.btn-line{border:2px solid #fff;border-radius:30px;color:#fff;font-family:"Audiowide",sans-serif;font-size:16px;display:flex;align-items:center;justify-content:center}
.btn-red{background:var(--red);border-radius:30px;color:#fff;font-family:"Audiowide",sans-serif;font-size:16px;display:flex;align-items:center;justify-content:center}

/* feature rows */
.photo{background:linear-gradient(135deg,#d8d6d4,#bfc3c8 50%,#e8e7e5)}
.feature-h{font-size:32px;color:var(--ink)}
.feature-rule{width:40px;height:3px;background:var(--red)}
.feature-copy{font-size:14px;line-height:26.5px;color:var(--text)}

/* testimonials */
.testi{left:0;top:2799px;width:1200px;height:418px;background:var(--mist)}
.portrait{left:155px;top:2870px;width:260px;height:260px;border-radius:50%;background:linear-gradient(160deg,#eceae8,#d7cfca 60%,#bdb6b2)}
.quote-badge{left:257px;top:3103px;width:56px;height:56px;border-radius:50%;background:var(--red)}
.testi-copy{left:470px;top:2954px;width:577px;font-size:14px;line-height:26.5px;text-align:justify}
.testi-name{left:467px;top:3106px;font-family:"Audiowide",sans-serif;font-size:16px;color:var(--red)}
.testi-name span{color:#444;font-size:14px}

/* footer */
.footer{left:0;top:3217px;width:1200px;height:379px;background:var(--footer)}
.footnav{left:310px;top:3266px;display:flex;gap:46px}
.rule{height:1px;background:var(--rule)}
.foot-h{font-family:"Roboto",sans-serif;font-weight:500;font-size:19px;color:#fff;letter-spacing:.5px}
.foot-copy{font-size:12.5px;line-height:24px;color:#fff}
.social{top:3395px;width:36px;height:36px;border:1.5px solid #fff;border-radius:50%}
.copyright{left:0;width:1200px;top:3541px;text-align:center;font-size:14px;color:#fff}
</style>
</head>
<body>

<!-- Hero -->
<div class="abs hero" role="img" aria-label="Night view of the San Francisco Bay Bridge and city skyline"></div>
<div class="abs brand" style="left:112px;top:44px">
  <div class="brand-square"></div>
  <div class="brand-name"><span class="l1">VANTOL</span><span class="l2">GROUP</span></div>
</div>
<nav class="abs topnav">
  <a href="#">HOME</a><a href="#">ABOUT US</a><a href="#">SERVICES</a><a href="#">BLUE MAPLE</a><a href="#">CONTACT US</a>
</nav>
<h1 class="abs hero-title display">VANTOL GROUP</h1>
<p class="abs hero-sub display">NEMO ENIM IPSAM VOLUPTATEM QUIA VOLUPTAS SIT ASPERNATUR AUT ODIT<br>AUT FUGIT, SED QUIA CONSEQUUNTUR MAGNI DOLORES</p>

<!-- Services -->
<h2 class="abs section-title display">OUR <span>SERVICES</span></h2>
<div class="abs title-rule"></div>

<div class="abs card red" style="left:112px">
  <svg viewBox="0 0 92 92" fill="none" stroke="#fff" stroke-width="3"><circle cx="22" cy="14" r="8" fill="#fff"/><path d="M12 28h20v34h-6v22h-8V62h-6z" fill="#fff"/><rect x="40" y="10" width="44" height="32"/><path d="M32 34l14-10"/><path d="M62 42v14M50 66l12-10 12 10"/></svg>
  <h3>EXECUTIVE</h3><div class="kind">PROTECTION</div>
  <p>Sed ut perspiciatis unde omn is iste natus error sit voluptatem doloremque laudantium</p>
  <span class="pill">LEARN MORE</span>
</div>
<div class="abs card dark" style="left:360px">
  <svg viewBox="0 0 92 92" fill="none" stroke="#fff" stroke-width="3"><path d="M42 6l32 12v24c0 22-14 36-32 44C24 78 10 64 10 42V18z"/><path d="M28 42l10 10 18-20"/><rect x="54" y="60" width="24" height="20" rx="2" fill="#232323"/><path d="M59 60v-7a7 7 0 0 1 14 0v7"/></svg>
  <h3>COVERT</h3><div class="kind">PROTECTION</div>
  <p>Sed ut perspiciatis unde omn is iste natus error sit voluptatem doloremque laudantium</p>
  <span class="pill">LEARN MORE</span>
</div>
<div class="abs card red" style="left:608px">
  <svg viewBox="0 0 92 92" fill="none" stroke="#fff" stroke-width="3"><rect x="32" y="6" width="28" height="80"/><rect x="10" y="36" width="22" height="50"/><rect x="60" y="30" width="22" height="56"/><path d="M36 56l10-8 10 8v30H36z"/><path d="M38 14h16M38 22h16M38 30h16M15 46h12M15 56h12M65 40h12M65 50h12"/></svg>
  <h3>RESIDENTIAL</h3><div class="kind">PROTECTION</div>
  <p>Sed ut perspiciatis unde omn is iste natus error sit voluptatem doloremque laudantium</p>
  <span class="pill">LEARN MORE</span>
</div>
<div class="abs card dark" style="left:856px">
  <svg viewBox="0 0 92 92" fill="none" stroke="#fff" stroke-width="3"><rect x="32" y="18" width="28" height="28"/><rect x="40" y="26" width="12" height="12"/><path d="M38 10v8M46 10v8M54 10v8M38 46v8M46 46v8M54 46v8M24 26h8M24 38h8M60 26h8M60 38h8"/><path d="M6 40l8 24 18 14M86 40l-8 24-18 14"/></svg>
  <h3>INTELLIGENCE</h3><div class="kind"></div>
  <p>Sed ut perspiciatis unde omn is iste natus error sit voluptatem doloremque laudantium</p>
  <span class="pill">LEARN MORE</span>
</div>

<!-- Welcome -->
<section class="abs welcome" role="img" aria-label="Faint bridge skyline under a deep red tint"></section>
<div class="abs welcome-photo" role="img" aria-label="Photo of business partners shaking hands"></div>
<div class="abs welcome-h display" style="top:1490px;font-size:32px">WELCOME</div>
<div class="abs welcome-h display" style="top:1538px;font-size:38px">VANTOL GROUP</div>
<p class="abs welcome-copy">Sed ut perspiciatis unde omnis iste natus error sit voluptatem accusantium doloremque laudantium, totam rem aperiam, eaque ipsa quae ab illo inventore veritatis et quasi architecto beatae vitae dicta sunt explicabo. Nemo enim ipsam voluptatem quia voluptas sit aspernatur aut odit aut fugit, sed quia dolores eos qui ratione voluptatem sequi nesciunt.</p>
<a class="abs btn-line" style="left:642px;top:1790px;width:172px;height:57px">READ MORE</a>

<!-- Training -->
<div class="abs photo" style="left:112px;top:2009px;width:488px;height:324px" role="img" aria-label="Team gathered around a computer in an office training session"></div>
<div class="abs" style="left:551px;top:2034px;width:49px;height:270px;background:var(--paper)"></div>
<h3 class="abs feature-h display" style="left:600px;top:2060px">TRAINING</h3>
<div class="abs feature-rule" style="left:600px;top:2106px"></div>
<p class="abs feature-copy" style="left:600px;top:2126px;width:470px">Sed ut perspiciatis unde omnis iste natus error sit voluptatem accusanti um doloremque laudantium, totam rem aperiam, eaque ipsa quae ab et quasi architecto beatae vitae dicta sunt explicabo.</p>
<a class="abs btn-red" style="left:600px;top:2229px;width:144px;height:50px">READ MORE</a>

<!-- Consulting -->
<div class="abs photo" style="left:600px;top:2403px;width:488px;height:323px" role="img" aria-label="Consultants shaking hands across a desk with a laptop"></div>
<div class="abs" style="left:600px;top:2428px;width:45px;height:279px;background:var(--paper)"></div>
<h3 class="abs feature-h display" style="left:165px;top:2454px">CONSULTING</h3>
<div class="abs feature-rule" style="left:165px;top:2500px"></div>
<p class="abs feature-copy" style="left:165px;top:2521px;width:470px">Sed ut perspiciatis unde omnis iste natus error sit voluptatem accusanti um doloremque laudantium, totam rem aperiam, eaque ipsa quae ab et quasi architecto beatae vitae dicta sunt explicabo.</p>
<a class="abs btn-red" style="left:165px;top:2623px;width:143px;height:50px">READ MORE</a>

<!-- Testimonials -->
<section class="abs testi"></section>
<div class="abs portrait" role="img" aria-label="Portrait of a smiling client"></div>
<div class="abs quote-badge"><svg viewBox="0 0 56 56" width="56" height="56" fill="#fff"><path d="M18 22h8v8l-4 8h-4l3-7h-3zM30 22h8v8l-4 8h-4l3-7h-3z"/></svg></div>
<h3 class="abs feature-h display" style="left:467px;top:2878px">TESTIMONIALS</h3>
<p class="abs testi-copy">Sed ut perspiciatis unde omnis iste natus error sit voluptatem accusantium doloremque laudantium, totam rem aperiam, eaque ipsa quae ab illo inventore veritatis et quasi architecto beatae vitae dicta sunt explicabo. Nemo enim ipsam voluptatem quia voluptas sit aspernatur aut odit aut fugit, sed quia consequuntur magni dolores eos qui ratione magnam omnis iste natus error sit aliquam quaerat voluptatem.</p>
<div class="abs testi-name">MARA ELLISON,<span>SED UT PERSPICIATIS UNDE</span></div>

<!-- Footer -->
<footer class="abs footer"></footer>
<nav class="abs footnav">
  <a href="#">HOME</a><a href="#">ABOUT US</a><a href="#">SERVICES</a><a href="#">BLUE MAPLE</a><a href="#">CONTACT US</a>
</nav>
<div class="abs rule" style="left:116px;top:3331px;width:972px"></div>
<div class="abs brand" style="left:140px;top:3390px">
  <div class="brand-square" style="width:46px;height:46px"></div>
  <div class="brand-name"><span class="l1" style="font-size:32px">VANTOL</span><span class="l2" style="font-size:15px;letter-spacing:9px;padding-left:38px">GROUP</span></div>
</div>
<div class="abs foot-h" style="left:442px;top:3376px">ADDRESS</div>
<p class="abs foot-copy" style="left:441px;top:3416px">Address: 2750 W. Harbor Lane<br>#410, Oakmont, CA 94612</p>
<div class="abs foot-h" style="left:661px;top:3376px">CONTACT US</div>
<p class="abs foot-copy" style="left:662px;top:3416px">415-555-0148<br>hello@vantolgroup.com</p>
<div class="abs social" style="left:868px"></div>
<div class="abs social" style="left:911px"></div>
<div class="abs social" style="left:954px"></div>
<div class="abs social" style="left:998px"></div>
<div class="abs social" style="left:1041px"></div>
<div class="abs rule" style="left:116px;top:3513px;width:972px"></div>
<p class="abs copyright">© Copyrights 2021 Vantol Group.All Rights Reserved.</p>

</body>
</html>
```